Creation of a construction/bricklaying business website

Following the template format of "Halloway 7", the following content would need to be included:
1. Landing page with 3 tiles that go to their own pages.
- Landing page to include background photo and description of services offered.
2. 3 tiles to include:
a) "Contact Us For A Free Quote or Friendly Discussion" Form (middle tile)
b) Case Studies and Testimonials
c) Certifications and Professional Membership
- Design logo to be used from previous SketchNestle project. Example of logo attached below, please access full JPG files from our account.

Target Market(s)

Prospective clients seeking construction work (bricklaying speciality)

Industry/Entity Type

Residential Construction

Coding

Coded - Design and coding required

Number of Pages Required

4 page

Font styles to use
Sans Serif

Colors

Designer to choose colors to be used in the design.

Requirements
Must have
• Following the template format of "Halloway 7", the following content would need to be included:
• 1. Landing parent page with 3 tiles that go to the 3 child pages.
• - Landing page to include background photo and description of services offered.
• 2. 3 tiles to include:
• a) "Contact Us For A Free Quote or Friendly Discussion" Form (middle tile)
• b) Case Studies and Testimonials (first tile / left side)
• c) Certifications and Professional Memberships (third tile / right side) (This should include logos of the relevant organisations being displayed. Specifically GQT and the Pillar Seal GQT).
• - Design logo to be used from previous SketchNestle project. Example of logo attached below, please access full JPG files from our account.
Nice to have
• Sleek and modern feel.
• Approachable in terms of how people can contact the company for a quote.
• Traditional pictures to give credibility and comfort around choosing this company.
Should not have
• Cheesy pictures
• Over-complicated
• Simple to use
• Easy URL domain name

```html
<!DOCTYPE html>
<html lang="en">
<head>
<meta charset="utf-8">
<title>R.T.Marlow Construction Ltd</title>
<link href="https://fonts.googleapis.com/css2?family=Work+Sans:wght@500;600;700&family=Nunito+Sans:wght@400;600&display=swap" rel="stylesheet">
<style>
:root{
  --blue:#0d5aa7;
  --blue-dark:#0a4a8c;
  --ink:#1e2226;
  --ink-soft:#2f3338;
  --tile:#e7ebed;
  --white:#ffffff;
  --footer-a:#2c3430;
  --footer-b:#1f2622;
}
*{margin:0;padding:0;box-sizing:border-box}
html,body{width:920px;height:1200px;overflow:hidden;background:var(--white)}
body{position:relative;font-family:"Nunito Sans",sans-serif;color:var(--ink)}
.hero{position:absolute;left:0;top:0;width:920px;height:315px;
  background:linear-gradient(180deg,#5a4a44 0%,#7a3f30 35%,#8a4636 60%,#5d5a56 100%)}
.hero-shade{position:absolute;inset:0;background:rgba(20,20,25,.28)}
.contact-chip{position:absolute;display:flex;align-items:center;gap:10px;color:var(--white);font-size:11.5px;line-height:1.45}
.chip-icon{width:29px;height:29px;border-radius:50%;background:var(--blue);display:flex;align-items:center;justify-content:center;flex:none}
.hero .phone{left:124px;top:14px}
.hero .email{left:626px;top:13px}
.brand{position:absolute;left:0;width:920px;text-align:center;color:var(--white);font-family:"Work Sans",sans-serif;font-weight:700}
.hero .brand{top:126px}
.brand .name{font-size:44px;letter-spacing:-.5px;line-height:1}
.brand .sub{font-size:17px;letter-spacing:3px;margin-top:6px}
.nav{position:absolute;top:315px;left:0;width:920px;height:35px;background:var(--blue)}
.nav a{position:absolute;top:10px;font-family:"Work Sans",sans-serif;font-weight:600;font-size:12px;color:var(--white);text-decoration:none;letter-spacing:.2px}
.nav a.current{color:var(--ink)}
.about-title{position:absolute;top:381px;width:920px;text-align:center;font-family:"Work Sans",sans-serif;font-weight:600;font-size:21px;color:var(--blue)}
.about-lead{position:absolute;top:422px;left:160px;width:600px;text-align:center;font-family:"Work Sans",sans-serif;font-weight:500;font-size:14.5px;line-height:17.5px;color:var(--ink-soft)}
.service{position:absolute;top:482px;width:110px;text-align:center}
.service-ring{width:78px;height:78px;margin:0 auto;border-radius:50%;border:2.5px solid var(--blue);background:radial-gradient(circle at 50% 40%,#fff 0%,#e6e6e6 100%);display:flex;align-items:center;justify-content:center;box-shadow:0 6px 5px -4px rgba(0,0,0,.18)}
.service-label{margin-top:22px;font-family:"Work Sans",sans-serif;font-weight:500;font-size:14.5px;line-height:17.5px;color:var(--ink-soft)}
.intro{position:absolute;left:128px;width:664px;text-align:center;font-size:12px;line-height:18.5px;color:var(--ink)}
.tile{position:absolute;top:754px;width:224px;height:208px;text-align:center;padding-top:22px}
.tile.shaded{background:var(--tile)}
.tile-icon{height:50px;display:flex;justify-content:center;align-items:center}
.tile-title{margin-top:14px;font-family:"Work Sans",sans-serif;font-weight:600;font-size:10.5px;line-height:14.5px;color:var(--ink)}
.tile-body{margin:12px 6px 0;font-size:10px;line-height:16.5px;color:var(--ink-soft)}
.tile-link{display:inline-block;margin-top:12px;font-family:"Work Sans",sans-serif;font-weight:600;font-size:11px;color:var(--blue);text-decoration:none}
.footer{position:absolute;left:0;top:1008px;width:920px;height:192px;background:linear-gradient(180deg,var(--footer-a),var(--footer-b));color:var(--white)}
.footer .brand{top:42px}
.footer .brand .name{font-size:19px}
.footer .brand .sub{font-size:7.5px;letter-spacing:1.5px;margin-top:2px}
.footer .contact-chip{top:86px;font-size:11px}
.copyright{position:absolute;left:146px;top:162px;font-size:11px}
.social{position:absolute;top:154px;display:flex;gap:4px;left:662px}
.social span{width:23px;height:23px;border-radius:50%;background:var(--white);display:block}
</style>
</head>
<body>

<header class="hero" role="img" aria-label="Photo of a newly built red brick garden wall in front of terraced houses">
  <div class="hero-shade"></div>
  <div class="contact-chip phone">
    <span class="chip-icon"><svg width="14" height="14" viewBox="0 0 24 24"><path fill="#fff" d="M6.6 10.8a15.1 15.1 0 0 0 6.6 6.6l2.2-2.2c.3-.3.7-.4 1-.2 1.1.4 2.3.6 3.6.6.6 0 1 .4 1 1V20c0 .6-.4 1-1 1A17 17 0 0 1 3 4c0-.6.4-1 1-1h3.5c.6 0 1 .4 1 1 0 1.3.2 2.5.6 3.6.1.3 0 .7-.2 1z"/></svg></span>
    <span>Call Us On<br>555.010.2468</span>
  </div>
  <div class="contact-chip email">
    <span class="chip-icon"><svg width="15" height="12" viewBox="0 0 20 14"><rect x="1" y="1" width="18" height="12" fill="none" stroke="#fff" stroke-width="1.8"/><path d="M1 1l9 7 9-7" fill="none" stroke="#fff" stroke-width="1.8"/></svg></span>
    <span>Email Us On<br>info@rtmarlowbuild.com</span>
  </div>
  <div class="brand">
    <div class="name">R.T.Marlow</div>
    <div class="sub">CONSTRUCTION LTD</div>
  </div>
</header>

<nav class="nav">
  <a class="current" href="#" style="left:131px">Home</a>
  <a href="#" style="left:182px">Case Studies &amp; Testimonials</a>
  <a href="#" style="left:363px">Contact Us For A Free Quote</a>
  <a href="#" style="left:552px">Certifications &amp; Professional Memberships</a>
</nav>

<main>
  <h1 class="about-title">About Us</h1>
  <p class="about-lead">R.T.Marlow Construction Ltd is a construction company that has expertise and experience in the following areas</p>

  <section class="services">
    <div class="service" style="left:108px">
      <div class="service-ring"><svg width="40" height="34" viewBox="0 0 40 34" fill="none" stroke="#333" stroke-width="1.6"><path d="M4 14L16 4l12 10"/><rect x="7" y="13" width="18" height="14"/><rect x="10" y="16" width="5" height="5"/><rect x="18" y="17" width="4" height="10"/><path d="M28 10h8v17h-11" stroke-dasharray="2 2"/><path d="M4 31h32"/></svg></div>
      <div class="service-label">Extensions</div>
    </div>
    <div class="service" style="left:226px">
      <div class="service-ring"><svg width="40" height="36" viewBox="0 0 40 36"><path d="M4 18L20 4l16 14" fill="none" stroke="#333" stroke-width="3"/><path d="M9 16v17h22V16" fill="none" stroke="#333" stroke-width="3"/><rect x="14" y="20" width="6" height="6" fill="#333"/><rect x="23" y="21" width="5" height="12" fill="#333"/></svg></div>
      <div class="service-label">New build /<br>New houses</div>
    </div>
    <div class="service" style="left:351px">
      <div class="service-ring"><svg width="48" height="34" viewBox="0 0 48 34" fill="#333"><rect x="2" y="2" width="10" height="5"/><rect x="2" y="9" width="44" height="5"/><rect x="2" y="16" width="44" height="5"/><rect x="2" y="23" width="44" height="5"/><rect x="2" y="30" width="44" height="3"/><g fill="#e6e6e6"><rect x="12" y="9" width="1.5" height="5"/><rect x="24" y="9" width="1.5" height="5"/><rect x="36" y="9" width="1.5" height="5"/><rect x="7" y="16" width="1.5" height="5"/><rect x="19" y="16" width="1.5" height="5"/><rect x="31" y="16" width="1.5" height="5"/><rect x="12" y="23" width="1.5" height="5"/><rect x="24" y="23" width="1.5" height="5"/><rect x="36" y="23" width="1.5" height="5"/></g></svg></div>
      <div class="service-label">Garden walls</div>
    </div>
    <div class="service" style="left:463px">
      <div class="service-ring"><svg width="44" height="38" viewBox="0 0 44 38" fill="none" stroke="#333" stroke-width="1.8"><rect x="2" y="4" width="26" height="30"/><path d="M2 12h26M2 20h26M2 28h26M12 4v8M20 12v8M12 20v8"/><path d="M26 14l12 14-3 3-12-14z" fill="#333"/></svg></div>
      <div class="service-label">Plastering</div>
    </div>
    <div class="service" style="left:583px">
      <div class="service-ring"><svg width="40" height="38" viewBox="0 0 40 38" fill="#333"><rect x="6" y="2" width="3" height="10"/><path d="M3 12h9l-4.5 10z"/><rect x="14" y="20" width="10" height="4"/><rect x="26" y="20" width="10" height="4"/><rect x="8" y="26" width="10" height="4"/><rect x="20" y="26" width="10" height="4"/><rect x="14" y="32" width="10" height="4"/><rect x="26" y="32" width="10" height="4"/></svg></div>
      <div class="service-label">Brickwork</div>
    </div>
    <div class="service" style="left:703px">
      <div class="service-ring"><svg width="40" height="38" viewBox="0 0 40 38" fill="#333"><rect x="5" y="2" width="10" height="3"/><rect x="8.5" y="4" width="3" height="18"/><path d="M4 22h12v8c0 4-3 6-6 6s-6-2-6-6z"/><path d="M18 36l6-12 5 4 4-2 5 10z"/></svg></div>
      <div class="service-label">Groundworks</div>
    </div>
  </section>

  <p class="intro" style="top:646px">We pride ourselves on attention to detail, pride in our completed project and client satisfaction. We believe in full transparency and this is reflected in the jobs we quote for you. We break down each step with both labour and materials cost so you can see exactly what you are paying for.</p>
  <p class="intro" style="top:714px">Feel free to get in touch and we can talk through what you are looking to achieve.</p>

  <section class="tiles">
    <article class="tile shaded" style="left:124px">
      <div class="tile-icon"><svg width="72" height="50" viewBox="0 0 72 50"><rect x="30" y="2" width="38" height="44" rx="3" fill="#fff" stroke="#1d4f8f" stroke-width="2"/><rect x="34" y="8" width="30" height="4" fill="#1d4f8f"/><circle cx="49" cy="27" r="8" fill="none" stroke="#1d4f8f" stroke-width="2.5"/><path d="M55 33l9 9" stroke="#1d4f8f" stroke-width="3"/><circle cx="14" cy="33" r="10" fill="#1d4f8f"/><circle cx="26" cy="26" r="8" fill="#8a8f95"/></svg></div>
      <h2 class="tile-title">Case Studies and<br>Testimonials</h2>
      <p class="tile-body">Ut wisi enim ad minim veniam, quis nostrud exerci tation ullamcorper suscipit lobortis nisl ut aliquip ex ea commodo consequat.</p>
      <a class="tile-link" href="#">Read More</a>
    </article>
    <article class="tile" style="left:348px">
      <div class="tile-icon"><svg width="48" height="50" viewBox="0 0 48 50" fill="none" stroke="#1d4f8f" stroke-width="2.2"><path d="M10 2h24l10 10v36H10z"/><path d="M34 2v10h10"/><path d="M20 24h18M20 30h18M20 36h18"/><path d="M3 36l5 7 9-14" stroke="#333" stroke-width="3"/></svg></div>
      <h2 class="tile-title">Contact Us For A<br>Free Quote</h2>
      <p class="tile-body">Ut wisi enim ad minim veniam, quis nostrud exerci tation ullamcorper suscipit lobortis nisl ut aliquip ex ea commodo consequat.</p>
      <a class="tile-link" href="#">Contact Us</a>
    </article>
    <article class="tile shaded" style="left:572px">
      <div class="tile-icon"><svg width="66" height="50" viewBox="0 0 66 50" role="img" aria-label="Membership badges of Pillar Seal GQT and GQT"><rect x="2" y="2" width="28" height="46" fill="#c8102e"/><rect x="36" y="2" width="28" height="46" fill="#c8102e"/></svg></div>
      <h2 class="tile-title">Certifications and Professional<br>Memberships</h2>
      <p class="tile-body">Ut wisi enim ad minim veniam, quis nostrud exerci tation ullamcorper suscipit lobortis nisl ut aliquip ex ea commodo consequat.</p>
      <a class="tile-link" href="#">Know More</a>
    </article>
  </section>
</main>

<footer class="footer" role="img" aria-label="Dimmed photo of a new housing development with trees and lawns">
  <div class="brand">
    <div class="name">R.T.Marlow</div>
    <div class="sub">CONSTRUCTION LTD</div>
  </div>
  <div class="contact-chip" style="left:146px">
    <span class="chip-icon"><svg width="12" height="15" viewBox="0 0 12 16"><path fill="#fff" d="M6 0a6 6 0 0 0-6 6c0 4.5 6 10 6 10s6-5.5 6-10a6 6 0 0 0-6-6zm0 8.3A2.3 2.3 0 1 1 6 3.7a2.3 2.3 0 0 1 0 4.6z"/></svg></span>
    <span>Street Name, City Name<br>State Zipcode</span>
  </div>
  <div class="contact-chip" style="left:393px">
    <span class="chip-icon"><svg width="14" height="14" viewBox="0 0 24 24"><path fill="#fff" d="M6.6 10.8a15.1 15.1 0 0 0 6.6 6.6l2.2-2.2c.3-.3.7-.4 1-.2 1.1.4 2.3.6 3.6.6.6 0 1 .4 1 1V20c0 .6-.4 1-1 1A17 17 0 0 1 3 4c0-.6.4-1 1-1h3.5c.6 0 1 .4 1 1 0 1.3.2 2.5.6 3.6.1.3 0 .7-.2 1z"/></svg></span>
    <span>Call Us On :<br>555.010.2468</span>
  </div>
  <div class="contact-chip" style="left:597px">
    <span class="chip-icon"><svg width="15" height="12" viewBox="0 0 20 14"><rect x="1" y="1" width="18" height="12" fill="none" stroke="#fff" stroke-width="1.8"/><path d="M1 1l9 7 9-7" fill="none" stroke="#fff" stroke-width="1.8"/></svg></span>
    <span>Email<br>info@rtmarlowbuild.com</span>
  </div>
  <p class="copyright">Copyright ©2018 R.T.Marlow Construction Ltd. All Rights Reserved.</p>
  <div class="social" aria-label="Social media links"><span></span><span></span><span></span><span></span></div>
</footer>

</body>
</html>
```